Business Card & Letterhead Design

We a financial advice company based in Australia. We provide advice to wealthy farmers.

We are changing our business name FROM Brightvale Financial TO Tallowmere Wealth and we need a new letterhead and double sided business card design

Attached is designs from our previous branding (Brightvale Financial) as it includes all the details we require on the new Tallowmere Wealth business cards and letterhead.

Need extra days to review

```html
<!DOCTYPE html>
<html lang="en">
<head>
<meta charset="utf-8">
<title>Tallowmere Wealth — Business Card</title>
<link rel="stylesheet" href="https://fonts.googleapis.com/css2?family=Montserrat:ital,wght@0,400;0,500;0,600;1,400&display=swap">
<style>
  :root {
    --bg-light: #e6e7e9;
    --bg-dark: #c4c5c8;
    --card-dark: #4a4a4a;
    --card-light: #ffffff;
    --ink: #444444;
    --ink-soft: #6a6a6a;
    --white: #ffffff;
  }
  * { margin: 0; padding: 0; box-sizing: border-box; }
  html, body { width: 1200px; height: 1200px; overflow: hidden; }
  body {
    position: relative;
    background: var(--bg-light);
    font-family: "Montserrat", sans-serif;
    color: var(--ink);
  }
  .backdrop { position: absolute; inset: 0; width: 1200px; height: 1200px; }
  .card { position: absolute; box-shadow: 0 3px 5px rgba(0,0,0,0.18); overflow: hidden; }

  /* Front */
  .card-front {
    left: 226px; top: 113px; width: 748px; height: 467px;
    background: var(--card-dark); color: var(--white); text-align: center;
  }
  .front-brand {
    position: absolute; left: 0; right: 0; top: 120px;
    display: flex; flex-direction: column; align-items: center; gap: 18px;
  }
  .brand-ring {
    width: 120px; height: 120px; border-radius: 50%;
    border: 5px solid var(--white);
  }
  .front-brand .brand-name { font-size: 22px; font-weight: 500; letter-spacing: 4px; }
  .front-brand .brand-name { display: none; }
  .brand-mark { position: absolute; left: 0; right: 0; top: 96px; display: flex; justify-content: center; }
  .brand-mark .brand-ring { width: 152px; height: 152px; display: flex; align-items: center; justify-content: center; }
  .brand-mark .brand-ring span { font-size: 15px; font-weight: 500; letter-spacing: 1.5px; line-height: 1.3; }
  .services { position: absolute; left: 0; right: 0; top: 252px; font-size: 22px; line-height: 39px; }
  .licence { position: absolute; left: 0; right: 0; top: 358px; font-size: 18.5px; line-height: 40px; }

  /* Back */
  .card-back {
    left: 224px; top: 619px; width: 752px; height: 471px;
    background: var(--card-light);
  }
  .back-brand {
    position: absolute; left: 40px; top: 42px; width: 320px;
    display: flex; flex-direction: column; align-items: center;
  }
  .back-brand .brand-ring { width: 84px; height: 84px; border: 3px solid var(--ink); }
  .back-brand .brand-name { margin-top: 12px; font-size: 26px; font-weight: 500; letter-spacing: 1.5px; color: var(--ink); }
  .back-brand .brand-tagline { margin-top: 2px; font-size: 10.5px; letter-spacing: 4.6px; color: var(--ink-soft); }

  .person { position: absolute; right: 46px; top: 68px; text-align: right; }
  .person-name { font-size: 22px; font-weight: 600; letter-spacing: 0.5px; }
  .person-name small { font-size: 12px; font-weight: 400; letter-spacing: 0; }
  .person-role { font-size: 18.5px; line-height: 29px; }

  .divider { position: absolute; left: 44px; right: 48px; top: 235px; height: 1.5px; background: var(--ink); }

  .contacts { position: absolute; left: 40px; top: 254px; list-style: none; }
  .contacts li { display: flex; align-items: center; height: 28.3px; font-size: 17px; }
  .contacts svg { width: 26px; height: 26px; margin-right: 8px; }
  .address { position: absolute; right: 46px; top: 254px; list-style: none; text-align: right; }
  .address li { height: 28.3px; line-height: 28.3px; font-size: 17px; }
  .address .firm { font-weight: 500; letter-spacing: 0.5px; }

  .band { position: absolute; left: 0; top: 423px; width: 752px; height: 48px; }
  .band-text {
    position: absolute; left: 0; right: 0; top: 427px; text-align: center;
    font-size: 16px; font-style: italic; color: var(--white); letter-spacing: 0.3px;
  }
</style>
</head>
<body>
  <svg class="backdrop" viewBox="0 0 1200 1200" aria-hidden="true">
    <polygon points="1200,0 1200,1200 0,1200" fill="var(--bg-dark)"/>
  </svg>

  <section class="card card-front" role="img" aria-label="Card front with faint geometric cube pattern on charcoal">
    <div class="brand-mark">
      <div class="brand-ring"><span>TALLOWMERE<br>WEALTH</span></div>
    </div>
    <p class="services">Life &amp; TPD Insurance | Income Protection<br>Financial Planning | Retirement Planning</p>
    <p class="licence">Meridian Advice Group Limited<br>Australian Financial Services Licensee License Number: 508213</p>
  </section>

  <section class="card card-back" role="img" aria-label="Card back with faint geometric cube pattern on white">
    <div class="back-brand">
      <div class="brand-ring"></div>
      <div class="brand-name">TALLOWMERE WEALTH</div>
      <div class="brand-tagline">STRATEGIC FINANCIAL ADVICE</div>
    </div>

    <div class="person">
      <div class="person-name">SAM REED <small>B.Ag.Ec. Dip F.P. CFP</small></div>
      <div class="person-role">Managing Director</div>
      <div class="person-role">Authorised Representative</div>
    </div>

    <div class="divider"></div>

    <ul class="contacts">
      <li><svg viewBox="0 0 26 26"><circle cx="13" cy="13" r="11.5" fill="none" stroke="#444" stroke-width="1.5"/><path d="M7 11c0-3 12-3 12 0l-2 1.5-2-1.5v-1h-4v1l-2 1.5z M8.5 13h9v5h-9z" fill="#444"/></svg>(07) 3000 4812</li>
      <li><svg viewBox="0 0 26 26"><circle cx="13" cy="13" r="11.5" fill="none" stroke="#444" stroke-width="1.5"/><rect x="9" y="7" width="8" height="4" fill="#444"/><rect x="7" y="11" width="12" height="6" fill="#444"/><rect x="9" y="15" width="8" height="4" fill="#fff" stroke="#444"/></svg>(07) 3000 4813</li>
      <li><svg viewBox="0 0 26 26"><circle cx="13" cy="13" r="11.5" fill="none" stroke="#444" stroke-width="1.5"/><rect x="9.5" y="6.5" width="7" height="13" rx="1.5" fill="none" stroke="#444" stroke-width="1.5"/><circle cx="13" cy="17" r="0.9" fill="#444"/></svg>0400 518 276</li>
      <li><svg viewBox="0 0 26 26"><circle cx="13" cy="13" r="11.5" fill="none" stroke="#444" stroke-width="1.5"/><rect x="7" y="9" width="12" height="8" fill="#444"/><path d="M7 9l6 5 6-5" fill="none" stroke="#fff" stroke-width="1.2"/></svg>sam@tallowmerewealth.com.au</li>
      <li><svg viewBox="0 0 26 26"><circle cx="13" cy="13" r="11.5" fill="none" stroke="#444" stroke-width="1.5"/><circle cx="13" cy="13" r="6.5" fill="none" stroke="#444" stroke-width="1.3"/><path d="M6.5 13h13M13 6.5c-3 3.5-3 9.5 0 13M13 6.5c3 3.5 3 9.5 0 13" fill="none" stroke="#444" stroke-width="1"/></svg>www.tallowmerewealth.com.au</li>
    </ul>

    <ul class="address">
      <li class="firm">TALLOWMERE WEALTH</li>
      <li>Suite 4A, 17 Harlow St.</li>
      <li>Riverside, QLD 4170</li>
      <li>P.O. Box 3318</li>
      <li>Eastvale, QLD 4170</li>
    </ul>

    <svg class="band" viewBox="0 0 752 48" aria-hidden="true">
      <polygon points="0,0 240,0 251,28 251,0 501,0 501,28 512,0 752,0 752,48 0,48" fill="var(--card-dark)"/>
      <polygon points="240,0 512,0 501,28 251,28" fill="var(--card-dark)"/>
      <polygon points="240,0 251,28 251,0" fill="#fff"/>
      <polygon points="512,0 501,28 501,0" fill="#fff"/>
    </svg>
    <div class="band-text">A Referral Built Business</div>
  </section>
</body>
</html>
```